Marlowe Group needs a business card

I would like the card to be simple but modern and elegant.
I like black and white.
or black and gold.
we are a private finance lender and also are involved in property and property developments.

please look at the business card photos i provided i would like M.G only one one side and all the other details on the other side use fonts that tie in with my theme.

Industry/Entity Type

Finance

Contact Information for Business Card

Marlowe Group (M.G) Daniel Marlowe M: 0413586207 E: danmarl@inboxmail.test

Font styles to use
Other font styles liked:
• Use fonts that would reflect our business

Colors
000000
ffffff

Requirements
Must have
• one side of details
• other side has either M.G or Marlowe Group like in the photos provided

```html
<!DOCTYPE html>
<html lang="en">
<head>
<meta charset="utf-8">
<title>Marlowe Group – Business Card</title>
<link rel="stylesheet" href="https://fonts.googleapis.com/css2?family=Cinzel:wght@400;700&family=Open+Sans:wght@400&display=swap">
<style>
  :root {
    --stage-top: #2c2c2c;
    --stage-bottom: #454545;
    --card-black: #000000;
    --gold: #f7d03c;
    --gold-deep: #e8b923;
    --card-yellow: #f8c535;
    --band-grey: #d4d4d4;
    --white: #ffffff;
  }
  * { margin: 0; padding: 0; box-sizing: border-box; }
  html, body { width: 1200px; height: 900px; overflow: hidden; }
  body {
    position: relative;
    background: linear-gradient(180deg, var(--stage-top) 0%, var(--stage-bottom) 100%);
    font-family: "Open Sans", Arial, sans-serif;
  }
  .card {
    position: absolute;
    top: 306px;
    width: 440px;
    height: 271px;
    border-radius: 10px;
    overflow: hidden;
    box-shadow: 0 2px 6px rgba(0,0,0,0.35);
  }
  .card--front { left: 149px; background: var(--card-black); }
  .card--back { left: 608px; background: var(--card-yellow); }

  .brand-mark {
    position: absolute;
    left: 14px;
    top: 70px;
    width: 208px;
    text-align: center;
    color: var(--gold);
    font-family: "Cinzel", Georgia, serif;
  }
  .brand-mark__initials {
    display: block;
    font-size: 58px;
    font-weight: 400;
    line-height: 1;
    letter-spacing: 2px;
  }
  .brand-mark__name {
    display: block;
    margin-top: 28px;
    font-size: 16px;
    font-weight: 400;
    letter-spacing: 0.5px;
  }

  .holder-name {
    position: absolute;
    left: 223px;
    top: 66px;
    color: var(--gold);
    font-family: "Cinzel", Georgia, serif;
    font-weight: 700;
    font-size: 19px;
    letter-spacing: 0.3px;
  }
  .contact-list {
    position: absolute;
    left: 226px;
    top: 151px;
    list-style: none;
    color: var(--white);
    font-size: 14px;
    line-height: 19px;
  }
  .contact-list li { display: flex; align-items: center; gap: 6px; }
  .contact-list svg { flex: none; }

  .card-band { position: absolute; left: 0; bottom: 0; }

  .back-pattern { position: absolute; inset: 0; background: var(--card-yellow); }
  .back-mark {
    position: absolute;
    left: 0; right: 0;
    top: 100px;
    text-align: center;
    color: var(--white);
    font-family: "Cinzel", Georgia, serif;
    font-size: 60px;
    font-weight: 400;
    line-height: 1;
    letter-spacing: 2px;
  }
</style>
</head>
<body>

  <section class="card card--front" aria-label="Card front">
    <div class="brand-mark">
      <span class="brand-mark__initials">M.G</span>
      <span class="brand-mark__name">Marlowe Group</span>
    </div>

    <h1 class="holder-name">Daniel Marlowe</h1>

    <ul class="contact-list">
      <li>
        <svg width="9" height="12" viewBox="0 0 9 12" aria-hidden="true">
          <rect x="1" y="0.5" width="7" height="11" rx="1.2" fill="none" stroke="var(--gold)" stroke-width="1.3"/>
          <rect x="3.3" y="9" width="2.4" height="1.2" fill="var(--gold)"/>
        </svg>
        <span>0413586207</span>
      </li>
      <li>
        <svg width="10" height="8" viewBox="0 0 10 8" aria-hidden="true">
          <rect x="0" y="0" width="10" height="8" fill="var(--gold)"/>
          <polyline points="0.5,0.8 5,4.6 9.5,0.8" fill="none" stroke="var(--card-black)" stroke-width="1"/>
        </svg>
        <span>danmarl@inboxmail.test</span>
      </li>
    </ul>

    <svg class="card-band" width="440" height="20" viewBox="0 0 440 20" aria-hidden="true">
      <rect x="0" y="6" width="215" height="14" fill="var(--band-grey)"/>
      <polygon points="224,0 440,0 440,20 208,20" fill="var(--gold)"/>
    </svg>
  </section>

  <section class="card card--back" aria-label="Card back">
    <div class="back-pattern" role="img" aria-label="Faint repeating monogram pattern in soft yellow"></div>
    <div class="back-mark">M.G</div>
  </section>

</body>
</html>
```